Website for new crypto research organization

See brief (attached). This is a pretty basic website with only a handful of pages + ability to collect email addresses.

```html
<!DOCTYPE html>
<html lang="en">
<head>
<meta charset="utf-8">
<title>Tidewell Labs — Crypto Research</title>
<link href="https://fonts.googleapis.com/css2?family=Ubuntu:wght@500;700&family=Montserrat:wght@400;500&family=Roboto:wght@400;500&display=swap" rel="stylesheet">
<style>
:root{
  --teal:#1a9a95;
  --blue:#2296d4;
  --ink:#222222;
  --text:#555a60;
  --mist:#eff1f4;
  --white:#ffffff;
  --line:#c9ccd0;
}
*{box-sizing:border-box;margin:0;padding:0}
html,body{width:1200px;height:3049px;overflow:hidden;background:var(--white)}
body{position:relative;font-family:'Montserrat',sans-serif;color:var(--ink)}
.abs{position:absolute}
.heading{font-family:'Ubuntu',sans-serif;font-weight:700}
.accent{color:var(--teal)}
.accent-blue{color:var(--blue)}
.pill{position:absolute;display:flex;align-items:center;justify-content:center;border-radius:24px;color:var(--white);font-family:'Ubuntu',sans-serif;font-weight:500;font-size:16px}

/* header */
.brand{position:absolute;left:112px;top:12px;width:184px;height:104px;display:flex;align-items:center;gap:10px}
.brand-mark{width:16px;height:16px;background:var(--teal);flex:none}
.brand-name{font-family:'Ubuntu',sans-serif;font-weight:700;font-size:24px;color:var(--teal);line-height:1.05}
.nav{position:absolute;top:52px;font-family:'Ubuntu',sans-serif;font-weight:500;font-size:16px;color:var(--ink)}
.nav.active{color:var(--teal)}
.nav.active::after{content:"";position:absolute;left:0;right:0;bottom:-7px;height:2px;background:var(--teal)}
.login{left:973px;top:43px;width:113px;height:42px;background:var(--teal)}

/* hero */
.hero{position:absolute;left:0;top:0;width:1200px;height:693px;background:linear-gradient(180deg,#fff 0%,#fff 55%,#eceef0 100%)}
.network{position:absolute;background:radial-gradient(ellipse at 50% 100%,#d8dadd 0%,rgba(235,236,238,.6) 50%,rgba(255,255,255,0) 80%)}
.hero-title{left:112px;top:213px;width:470px;font-size:44px;line-height:52px}
.quote{left:112px;top:482px;width:141px;height:42px;background:var(--teal)}
.report{left:267px;top:482px;width:226px;height:42px;background:var(--blue)}
.hero-art{left:580px;top:180px;width:568px;height:376px;background:radial-gradient(ellipse at 65% 50%,#e5a03a 0%,#c9413b 25%,#3a6fb5 45%,#9aa0a6 70%,rgba(255,255,255,0) 90%)}

/* research */
.research{position:absolute;left:0;top:693px;width:1200px;height:467px;background:var(--mist)}
.section-title{position:absolute;left:0;width:1200px;text-align:center;font-size:44px}
.step{position:absolute;top:171px;width:238px;height:168px;border-radius:32px;display:flex;align-items:center;justify-content:center;z-index:1}
.step.teal{background:var(--teal)}
.step.blue{background:var(--blue)}
.step-label{position:absolute;top:356px;width:238px;text-align:center;font-family:'Ubuntu',sans-serif;font-weight:500;font-size:22px}
.connector{position:absolute;top:234px;width:42px;height:42px;border-radius:50%;background:var(--white);display:flex;align-items:center;justify-content:center;z-index:2}

/* about */
.about-photo{left:112px;top:1226px;width:444px;height:444px;border-radius:50%;border:6px solid #1f98b0;background:linear-gradient(135deg,#3b3f6b 0%,#7a5b8a 35%,#2c86b8 60%,#585c63 100%)}
.about-title{left:599px;top:1216px;font-size:46px}
.about-copy{left:599px;width:489px;font-size:15px;line-height:21.5px;color:var(--text);text-align:justify}
.learn{left:597px;top:1628px;width:141px;height:43px;background:var(--teal)}

/* news */
.news{position:absolute;left:0;top:1757px;width:1200px;height:527px;background:var(--mist)}
.card{position:absolute;top:151px;width:311px;height:290px;background:var(--white);border:2px solid var(--teal);border-radius:36px;padding:30px 28px}
.card-date{display:flex;align-items:center;gap:7px;font-family:'Ubuntu',sans-serif;font-weight:500;font-size:16px;color:var(--teal)}
.card-title{margin-top:18px;font-family:'Ubuntu',sans-serif;font-weight:500;font-size:23px;line-height:30px}
.card-text{margin-top:14px;font-size:14.5px;line-height:21.5px;color:var(--text)}
.card-link{display:inline-block;margin-top:12px;font-family:'Ubuntu',sans-serif;font-weight:500;font-size:15px;color:var(--teal);text-decoration:underline}

/* newsletter */
.newsletter{position:absolute;left:0;top:2284px;width:1200px;height:310px;background:linear-gradient(180deg,#1356b8 0%,#1a6fd0 45%,#0f8fd8 80%,#0b5fb4 100%)}
.subscribe-field{position:absolute;left:269px;top:157px;width:661px;height:62px;border-radius:31px;background:var(--white);border:3px solid var(--white)}
.subscribe-field span{position:absolute;left:34px;top:18px;font-size:15px;color:#555}
.subscribe-btn{position:absolute;right:2px;top:2px;width:182px;height:52px;border-radius:26px;background:var(--teal);color:var(--white);font-family:'Ubuntu',sans-serif;font-weight:500;font-size:15px;display:flex;align-items:center;justify-content:center}

/* footer */
.foot-brand{left:109px;top:2684px;width:222px;height:128px;display:flex;align-items:center;justify-content:center;gap:10px}
.social{position:absolute;top:2838px;width:32px;height:32px;border-radius:50%;border:2px solid var(--teal)}
.foot-head{position:absolute;top:2680px;font-family:'Roboto',sans-serif;font-weight:500;font-size:17px}
.contact-icon{position:absolute;left:434px;width:38px;height:38px;border-radius:50%;border:2px solid var(--teal);display:flex;align-items:center;justify-content:center}
.contact-text{position:absolute;left:490px;font-family:'Roboto',sans-serif;font-size:12.5px;line-height:19px;color:#333}
.field{position:absolute;border:1px solid var(--line);font-family:'Roboto',sans-serif;font-size:12px;color:#555;padding:9px 12px}
.submit{position:absolute;left:1018px;top:2902px;width:83px;height:30px;border-radius:4px;background:var(--teal);color:var(--white);font-family:'Roboto',sans-serif;font-weight:500;font-size:12px;display:flex;align-items:center;justify-content:center}
.rule{position:absolute;left:99px;top:2958px;width:1002px;height:1px;background:#bbb}
.legal{position:absolute;left:0;top:2995px;width:1200px;text-align:center;font-family:'Roboto',sans-serif;font-size:12px;color:#444}
</style>
</head>
<body>

<!-- hero -->
<section class="hero">
  <div class="network" role="img" aria-label="Soft grey connected-dots network backdrop" style="left:0;top:380px;width:1200px;height:313px"></div>
</section>

<header>
  <div class="brand"><span class="brand-mark"></span><span class="brand-name">Tidewell Labs</span></div>
  <nav>
    <span class="nav active" style="left:471px">Home</span>
    <span class="nav" style="left:544px">About</span>
    <span class="nav" style="left:619px">Research</span>
    <span class="nav" style="left:718px">News</span>
    <span class="nav" style="left:788px">Careers</span>
    <span class="nav" style="left:876px">Contact</span>
  </nav>
  <div class="pill login">
    <svg width="12" height="14" viewBox="0 0 12 14" style="margin-right:6px"><circle cx="6" cy="4" r="3.2" fill="#fff"/><path d="M0 14c0-4 2.5-6 6-6s6 2 6 6z" fill="#fff"/></svg>Login
  </div>
</header>

<h1 class="abs heading hero-title">We are very small startup research organization focused on crypto / digital assets</h1>
<div class="pill quote">Get a Quote</div>
<div class="pill report">Recent Research Report</div>
<div class="abs hero-art" role="img" aria-label="Colourful graffiti wall being revealed behind a grey curtain"></div>
<svg class="abs" style="left:586px;top:603px" width="30" height="44" viewBox="0 0 30 44"><rect x="2" y="2" width="26" height="40" rx="13" fill="none" stroke="#222" stroke-width="2"/><path d="M15 9v16M9 19l6 6 6-6" fill="none" stroke="#222" stroke-width="2"/></svg>

<!-- research process -->
<section class="research">
  <h2 class="section-title heading" style="top:79px"><span class="accent">Research</span> <span class="accent-blue">Process</span></h2>

  <div class="step teal" style="left:112px">
    <svg width="120" height="116" viewBox="0 0 120 116" fill="none" stroke="#fff" stroke-width="3"><rect x="14" y="6" width="62" height="84"/><path d="M8 14v84h62"/><path d="M26 22h22M26 34h38M26 46h38M26 58h24M26 70h20"/><rect x="54" y="18" width="14" height="12"/><circle cx="82" cy="84" r="16"/><path d="M94 96l16 16"/></svg>
  </div>
  <div class="connector" style="left:330px"><svg width="24" height="14" viewBox="0 0 24 14" fill="none" stroke="#222" stroke-width="2"><path d="M2 8c6-8 14-8 20 0M17 9l5-1 0-5"/></svg></div>

  <div class="step blue" style="left:357px">
    <svg width="120" height="116" viewBox="0 0 120 116" fill="none" stroke="#fff" stroke-width="3"><rect x="8" y="6" width="82" height="76" rx="6"/><path d="M8 18h82"/><circle cx="30" cy="44" r="12"/><path d="M30 32v12h12"/><path d="M58 60V44M68 60V36M78 60V28"/><circle cx="78" cy="80" r="20"/><path d="M92 94l18 16"/></svg>
  </div>
  <div class="connector" style="left:578px"><svg width="24" height="14" viewBox="0 0 24 14" fill="none" stroke="#222" stroke-width="2"><path d="M2 8c6-8 14-8 20 0M17 9l5-1 0-5"/></svg></div>

  <div class="step teal" style="left:605px">
    <svg width="116" height="116" viewBox="0 0 116 116" fill="none" stroke="#fff" stroke-width="3"><circle cx="58" cy="54" r="50"/><ellipse cx="58" cy="54" rx="22" ry="50"/><path d="M8 54h100M16 28h84M16 80h84"/><circle cx="58" cy="38" r="16"/><path d="M58 54v50"/></svg>
  </div>
  <div class="connector" style="left:824px"><svg width="24" height="14" viewBox="0 0 24 14" fill="none" stroke="#222" stroke-width="2"><path d="M2 8c6-8 14-8 20 0M17 9l5-1 0-5"/></svg></div>

  <div class="step blue" style="left:851px">
    <svg width="124" height="100" viewBox="0 0 124 100" fill="none" stroke="#fff" stroke-width="3"><path d="M62 16C48 6 24 6 8 10v76c16-4 40-4 54 6 14-10 38-10 54-6V10C100 6 76 6 62 16z"/><path d="M62 16v76"/><path d="M18 26h32M18 38h32M18 50h28M74 26h30"/><circle cx="88" cy="58" r="16"/><path d="M100 70l16 16"/></svg>
  </div>

  <div class="step-label" style="left:112px">Nemo enim ipsam</div>
  <div class="step-label" style="left:357px">Nemo enim ipsam</div>
  <div class="step-label" style="left:605px">Nemo enim ipsam</div>
  <div class="step-label" style="left:851px">Nemo enim ipsam</div>
</section>

<!-- about -->
<div class="abs about-photo" role="img" aria-label="Night photo of a narrow city laneway covered in graffiti"></div>
<h2 class="abs heading about-title accent">About us</h2>
<p class="abs about-copy" style="top:1286px">Lorem ipsum dolor sit amet, consectetur adipiscing elit, sed do eiusmod tempor incididunt ut labore et dolore magna aliqua. Ut enim ad minim veniam, quis nostrud exercitation ullamco laboris nisi ut aliquip ex ea commodo consequat. Duis aute irure dolor in reprehenderit in volup tate velit esse cillum dolore eu fugiat nulla pariatur. Excepteur sint occa ecat cupidatat non proident, sunt in culpa qui officia deserunt mollit anim id est laborum.</p>
<p class="abs about-copy" style="top:1458px">Lorem ipsum dolor sit amet, consectetur adipiscing elit, sed do eiusmod tempor incididunt ut labore et dolore magna aliqua. Ut enim ad minim veniam, quis nostrud exercitation ullamco laboris nisi ut aliquip ex ea commodo consequat. Duis aute irure dolor in reprehenderit in volupta te velit esse cillum dolore eu fugiat nulla pariatur. Excepteur sint occae cat cupidatat non proident, sunt in culpa qui officia deserunt mollit anim id est laborum.</p>
<div class="pill learn">Learn more</div>

<!-- news -->
<section class="news">
  <div class="network" role="img" aria-label="Soft grey connected-dots network backdrop" style="left:0;top:260px;width:1200px;height:267px"></div>
  <h2 class="section-title heading accent" style="top:58px">Latest News</h2>

  <article class="card" style="left:111px">
    <div class="card-date"><svg width="14" height="14" viewBox="0 0 14 14" fill="none" stroke="#1a9a95" stroke-width="1.6"><rect x="1" y="2.5" width="12" height="10.5"/><path d="M1 6h12M4 1v3M10 1v3"/></svg>Jan 28, 2022</div>
    <h3 class="card-title">Lorem ipsum dolor sit amet, consectetur</h3>
    <p class="card-text">Lorem ipsum dolor sit amet, conse ctetur adipiscing elit, sed do eiusm od tempor incididunt ut labore et dolore magna aliqua.</p>
    <span class="card-link">View Articles</span>
  </article>
  <article class="card" style="left:444px">
    <div class="card-date"><svg width="14" height="14" viewBox="0 0 14 14" fill="none" stroke="#1a9a95" stroke-width="1.6"><rect x="1" y="2.5" width="12" height="10.5"/><path d="M1 6h12M4 1v3M10 1v3"/></svg>Jan 28, 2022</div>
    <h3 class="card-title">Lorem ipsum dolor sit amet, consectetur</h3>
    <p class="card-text">Lorem ipsum dolor sit amet, conse ctetur adipiscing elit, sed do eiusm od tempor incididunt ut labore et dolore magna aliqua.</p>
    <span class="card-link">View Articles</span>
  </article>
  <article class="card" style="left:777px">
    <div class="card-date"><svg width="14" height="14" viewBox="0 0 14 14" fill="none" stroke="#1a9a95" stroke-width="1.6"><rect x="1" y="2.5" width="12" height="10.5"/><path d="M1 6h12M4 1v3M10 1v3"/></svg>Jan 28, 2022</div>
    <h3 class="card-title">Lorem ipsum dolor sit amet, consectetur</h3>
    <p class="card-text">Lorem ipsum dolor sit amet, conse ctetur adipiscing elit, sed do eiusm od tempor incididunt ut labore et dolore magna aliqua.</p>
    <span class="card-link">View Articles</span>
  </article>
</section>

<!-- newsletter -->
<section class="newsletter" role="img" aria-label="Blue digital particle wave backdrop">
  <h2 class="section-title heading" style="top:72px;color:#fff">Subscribe Our Newsletter</h2>
  <div class="subscribe-field"><span>Email address</span><div class="subscribe-btn">SUBSCRIBE</div></div>
</section>

<!-- footer -->
<div class="abs foot-brand"><span class="brand-mark"></span><span class="brand-name" style="font-size:26px">Tidewell Labs</span></div>
<span class="social" style="left:166px"></span>
<span class="social" style="left:203px;background:var(--teal)"></span>
<span class="social" style="left:240px"></span>

<div class="foot-head" style="left:434px">Contact Information</div>
<div class="contact-icon" style="top:2723px"><svg width="12" height="16" viewBox="0 0 12 16" fill="none" stroke="#1a9a95" stroke-width="1.6"><path d="M6 15S1 9 1 6a5 5 0 0 1 10 0c0 3-5 9-5 9z"/><circle cx="6" cy="6" r="1.8"/></svg></div>
<div class="contact-text" style="top:2726px;font-weight:500">Lorem ipsum dolor sit ame<br>t, consectetur adipiscing</div>
<div class="contact-icon" style="top:2774px"><svg width="16" height="16" viewBox="0 0 16 16" fill="none" stroke="#1a9a95" stroke-width="1.6"><path d="M3 1l3 3-2 2c1 2.5 3.5 5 6 6l2-2 3 3-2 2C7 14 2 9 1 3z"/></svg></div>
<div class="contact-text" style="top:2784px">Phone : +1 888 888 8888</div>
<div class="contact-icon" style="top:2824px;background:var(--teal)"><svg width="16" height="12" viewBox="0 0 16 12" fill="none" stroke="#fff" stroke-width="1.6"><rect x="1" y="1" width="14" height="10"/><path d="M1 1l7 6 7-6"/></svg></div>
<div class="contact-text" style="top:2834px">Email : info@company.com</div>
<div class="contact-icon" style="top:2876px"><svg width="16" height="16" viewBox="0 0 16 16" fill="none" stroke="#1a9a95" stroke-width="1.6"><rect x="1" y="5" width="14" height="10"/><rect x="4" y="1" width="8" height="4"/><path d="M4 9h8M4 12h8"/></svg></div>
<div class="contact-text" style="top:2886px">Fax: 0661-55012</div>

<div class="foot-head" style="left:709px">Get In Touch:</div>
<div class="field" style="left:711px;top:2723px;width:180px;height:31px">Name :</div>
<div class="field" style="left:901px;top:2723px;width:197px;height:31px">Phone :</div>
<div class="field" style="left:711px;top:2767px;width:387px;height:31px">Email :</div>
<div class="field" style="left:711px;top:2811px;width:387px;height:69px">Message :</div>
<div class="submit">SUBMIT</div>

<div class="rule"></div>
<div class="legal">Copyrights © 2022, Company name. All Rights Reserved. &nbsp;|&nbsp; Privacy policy</div>

</body>
</html>
```